New letter head for Air Conditioning business

We need a new professional letter head design to suit our new re-branded air conditioning business. Our new logo is attached

```html
<!DOCTYPE html>
<html lang="en">
<head>
<meta charset="utf-8">
<title>Vela Air Conditioning &amp; Refrigeration – Letterhead</title>
<link rel="stylesheet" href="https://fonts.googleapis.com/css2?family=Lato:wght@300;400;700&display=swap">
<style>
  :root{
    --backdrop:#e9e9e9;
    --paper:#f7f7f7;
    --ink:#3a3a3a;
    --ink-soft:#5a5a5a;
    --brand-green:#4caf6e;
    --brand-red:#d95a4c;
    --sig-tone:#e6e6e6;
  }
  *{box-sizing:border-box;margin:0;padding:0}
  html,body{width:1200px;height:795px;overflow:hidden;background:var(--backdrop)}
  body{font-family:"Lato",Arial,sans-serif;color:var(--ink)}
  .letterhead{
    position:absolute;left:338px;top:27px;width:524px;height:741px;
    background:var(--paper);box-shadow:0 6px 24px rgba(0,0,0,.12);
  }
  .edge-band{position:absolute;left:0;top:0;width:5px;height:100%;background:var(--brand-green)}
  .edge-block{position:absolute;left:0;top:640px;width:26px;height:64px;background:var(--brand-red)}
  .brand{position:absolute;left:46px;top:46px;display:flex;align-items:center;gap:8px}
  .brand-mark{width:12px;height:12px;background:var(--brand-green)}
  .brand-name{font-weight:700;font-size:22px;letter-spacing:3px;color:var(--ink)}
  .brand-tag{position:absolute;left:66px;top:74px;font-size:5px;letter-spacing:1.2px;color:var(--brand-green);font-weight:700;text-transform:uppercase}
  .letter{position:absolute;left:76px;top:150px;width:400px;font-size:7.6px;line-height:11px;font-weight:300;color:var(--ink-soft)}
  .date{margin-bottom:12px}
  .recipient strong{font-weight:700;color:var(--ink)}
  .salutation{margin:14px 0 14px}
  .letter p.body{margin-bottom:14px}
  .closing{margin-top:18px}
  .signature{display:block;width:150px;height:34px;margin-top:6px;background:var(--sig-tone);border-radius:3px}
  .contact{position:absolute;left:76px;top:636px;font-size:8px;line-height:11px;color:var(--ink)}
  .contact .line{display:flex;align-items:center;gap:4px}
  .contact svg{width:7px;height:7px}
  .website{position:absolute;right:40px;top:640px;font-size:8px;color:var(--ink)}
  .website b{color:var(--brand-green);font-weight:700}
</style>
</head>
<body>
<main class="letterhead">
  <div class="edge-band"></div>
  <div class="edge-block"></div>

  <div class="brand">
    <span class="brand-mark"></span>
    <span class="brand-name">VELA</span>
  </div>
  <div class="brand-tag">Air Conditioning &amp; Refrigeration</div>

  <section class="letter">
    <div class="date">01 January 2050</div>
    <div class="recipient">
      <strong>Harbourline Trading Pty Ltd.</strong><br>
      PO Box 4120 Kestrel St<br>
      Brookvale City 4120
    </div>
    <div class="salutation">Dear Daniel Ashcombe,</div>
    <p class="body">Lorem ipsum dolor sit amet, consectetuer adipiscing elit, sed diam nonummy nibh euismod tincidunt ut laoreet dolore magna aliquam erat volutpat. Ut wisi enim ad minim veniam, quis nostrud exerci tation ullamcorper suscipit lobortis nisl ut aliquip ex ea commodo consequat. Duis dolore te feugait nulla facilisi. Nam liber tempor cum soluta nobis eleifend option congue nihil imperdiet doming id quod mazim placerat facer possim assum. Lorem ipsum dolor sit amet, consectetuer adipiscing elit, sed diam nonummy nibh euismod tincidunt ut laoreet dolore magna aliquam erat volutpat. Ut wisi enim ad minim veniam, quis nostrud exerci tation ullamcorper suscipit lobortis nisl ut aliquip ex ea commodo consequat.</p>
    <p class="body">Consectetuer adipiscing elit, sed diam nonummy nibh euismod tincidunt ut laoreet dolore magna aliquam erat volutpat. Ut wisi enim ad minim veniam, quis nostrud exerci tation ullamcorper suscipit lobortis nisl ut aliquip ex ea commodo consequat. Consectetuer adipiscing elit, sed diam nonummy nibh euismod tincidunt ut laoreet dolore magna aliquam erat volutpat. Ut wisi enim ad minim veniam, quis nostrud exerci tation ullamcorper suscipit lobortis nisl ut aliquip ex ea commodo consequat.</p>
    <p class="body">Consectetuer adipiscing elit, sed diam nonummy nibh euismod tincidunt ut laoreet dolore magna aliquam erat volutpat. Ut wisi enim ad minim veniam, quis nostrud exerci tation ullamcorper suscipit lobortis nisl ut aliquip ex ea commodo consequat. Consectetuer adipiscing elit, sed diam nonummy nibh euismod tincidunt ut laoreet dolore magna aliquam erat volutpat. Ut wisi enim ad minim veniam, quis nostrud exerci tation ullamcorper suscipit lobortis nisl ut aliquip ex ea commodo consequat.</p>
    <div class="closing">Sincerely Yours</div>
    <span class="signature" role="img" aria-label="Handwritten signature of Marcus Ellery Vaughn"></span>
  </section>

  <address class="contact" style="font-style:normal">
    <div>Unit 18, Level 2</div>
    <div>Ferncourt Ave</div>
    <div>Riverton 5021</div>
    <div class="line">
      <svg viewBox="0 0 10 10" aria-hidden="true"><path d="M2 1l2 2-1 1.5c.8 1.3 1.7 2.2 3 3L7.5 6l2 2-1.5 1.5C4.5 9 1 5.5.5 2z" fill="var(--brand-green)"/></svg>
      (+1) 555.014.2290
    </div>
    <div class="line">
      <svg viewBox="0 0 10 10" aria-hidden="true"><rect x="0.5" y="2" width="9" height="6" fill="var(--brand-green)"/><path d="M.5 2L5 5.5 9.5 2" fill="none" stroke="var(--paper)" stroke-width="1"/></svg>
      hello@velacooling.example
    </div>
  </address>

  <div class="website">www.<b>velacooling</b>.example</div>
</main>
</body>
</html>
```